Business Card Design

Hi I need a business card designed, we already have the business name logo artwork and would like some concept ideas for the Bus Card layout.
On the back of the card i want to include the products and services that we offer.
We are a Plastics Sheeting manufacture based in Perth Australia.

                                       

We need a BC design for a company called Tarvo Plastics based in Perth Australia.

We supply from DIY to Trade & Industrial  Engineering Markets.

We specialise in:

·         Cut to size panels  (all shapes and sizes)

·         Plastics fabrication & Welding

·         Custom Designs

·         Plastic Repairs

·         PVC Pipe Slotting & PVC Pipe Threading

·         Supplier of all types of engineering plastics and profiles.

Including:           Acrylic / Clarvene

                               Polycarbonate / Dorvil

                               Prismatic Light Diffuser

                               Vantrib

                               HDPE / UHMWPE

                               PVC / PVC Foam

                               Nylon

                               HIPS

```html
<!DOCTYPE html>
<html lang="en">
<head>
<meta charset="utf-8">
<title>Tarvo Plastics – Business Card</title>
<link rel="stylesheet" href="https://fonts.googleapis.com/css2?family=Source+Sans+3:wght@400;600;700&display=swap">
<style>
  :root {
    --navy: #1d2f6f;
    --orange: #ee7d22;
    --grey-text: #5a5d63;
    --silver-light: #f1f2f4;
    --silver-mid: #cfd2d6;
    --silver-dark: #b5b9be;
    --backdrop: #e6e6e4;
    --divider: #9ea2a8;
  }
  * { box-sizing: border-box; margin: 0; padding: 0; }
  html, body { width: 1200px; height: 720px; overflow: hidden; }
  body {
    background: var(--backdrop);
    font-family: "Source Sans 3", "Myriad Pro", sans-serif;
    color: var(--grey-text);
    position: relative;
  }
  .card {
    position: absolute;
    width: 540px;
    height: 330px;
    top: 195px;
    border-radius: 3px;
    background:
      radial-gradient(ellipse at 50% 45%, var(--silver-light) 0%, var(--silver-mid) 55%, var(--silver-dark) 100%);
    box-shadow: 0 4px 14px rgba(0,0,0,.18);
    overflow: hidden;
  }
  .card--front { left: 40px; }
  .card--back { left: 620px; }

  .brand {
    display: flex;
    align-items: center;
    gap: 10px;
    color: var(--navy);
    font-weight: 700;
    line-height: 1;
    white-space: nowrap;
  }
  .brand__mark {
    width: 14px; height: 14px;
    background: var(--navy);
  }

  /* Front */
  .card--front .brand { position: absolute; left: 34px; top: 38px; font-size: 48px; }
  .front__identity { position: absolute; left: 34px; top: 176px; width: 260px; }
  .person__name { color: var(--navy); font-weight: 700; font-size: 17px; line-height: 1.1; }
  .person__title { color: var(--orange); font-size: 13px; margin-bottom: 6px; }
  .address { font-size: 13.5px; line-height: 1.3; margin-top: 8px; }
  .front__divider {
    position: absolute; left: 330px; top: 150px; width: 1px; height: 140px;
    background: var(--orange);
  }
  .contact { position: absolute; left: 346px; top: 150px; font-size: 13px; line-height: 1.35; }
  .contact__row { display: flex; align-items: center; gap: 6px; }
  .contact__row svg { width: 11px; height: 11px; fill: var(--navy); flex: none; }
  .contact__legal { margin-top: 10px; }

  /* Back */
  .card--back .brand { position: absolute; left: 0; right: 0; top: 26px; justify-content: center; font-size: 40px; }
  .back__headline {
    position: absolute; left: 20px; right: 20px; top: 84px;
    text-align: center; color: var(--navy); font-weight: 700; font-size: 14px; line-height: 1.25;
  }
  .services { position: absolute; left: 30px; top: 134px; width: 300px; }
  .materials { position: absolute; left: 362px; top: 134px; width: 170px; }
  .list-heading { color: var(--navy); font-weight: 700; font-size: 17px; margin-bottom: 4px; }
  .bullet-list { list-style: none; font-size: 13px; line-height: 1.3; }
  .bullet-list li { position: relative; padding-left: 12px; margin-bottom: 2px; }
  .bullet-list li::before {
    content: ""; position: absolute; left: 0; top: 6px;
    width: 5px; height: 5px; border-radius: 50%; background: var(--orange);
  }
  .bullet-inline::before {
    content: ""; display: inline-block; width: 5px; height: 5px; border-radius: 50%;
    background: var(--orange); margin: 0 6px 2px 8px;
  }
  .back__divider {
    position: absolute; left: 345px; top: 138px; width: 1px; height: 150px;
    background: var(--divider);
  }
</style>
</head>
<body>

<section class="card card--front" aria-label="Business card front">
  <div class="brand"><span class="brand__mark"></span>Tarvo Plastics</div>

  <div class="front__identity">
    <p class="person__name">Your Name</p>
    <p class="person__title">Title</p>
    <p class="address">Unit 4/18 Kestrel Circuit<br>Hollis Vale WA 6181</p>
    <p class="address">PO Box 2240<br>Hollis Vale DC WA 6981</p>
  </div>

  <div class="front__divider"></div>

  <div class="contact">
    <p class="contact__row">
      <svg viewBox="0 0 12 12" aria-hidden="true"><path d="M2.5 1 4.5 3 3.5 4.5c.8 1.6 2 2.8 3.5 3.6L8.5 7l2 2-1.5 2C5 10.6 1.4 7 1 3z"/></svg>
      08 5550 2011
    </p>
    <p class="contact__row">
      <svg viewBox="0 0 12 12" aria-hidden="true"><path d="M3.5 0h5a1 1 0 0 1 1 1v10a1 1 0 0 1-1 1h-5a1 1 0 0 1-1-1V1a1 1 0 0 1 1-1zm0 1.5v7.5h5V1.5z"/></svg>
      0400 555 789
    </p>
    <p class="contact__row">
      <svg viewBox="0 0 12 12" aria-hidden="true"><path d="M3 0h6v3H3zM1 4h10a1 1 0 0 1 1 1v4H10v3H2V9H0V5a1 1 0 0 1 1-1zm2 4v3h6V8z"/></svg>
      08 5550 2022
    </p>
    <p class="contact__row">
      <svg viewBox="0 0 12 12" aria-hidden="true"><path d="M0 2h12v8H0zm1 1v.3l5 3.2 5-3.2V3z"/></svg>
      sales@tarvoplastics.com.au
    </p>
    <p class="contact__legal">Tarvo Holdings Pty Ltd<br>T/A Tarvo Plastics ABN: TBA</p>
  </div>
</section>

<section class="card card--back" aria-label="Business card back">
  <div class="brand"><span class="brand__mark"></span>Tarvo Plastics</div>

  <p class="back__headline">The Products And Services That We Offer<br>Are Supplied From Diy To Trade &amp; Industrial Engineering Markets</p>

  <div class="services">
    <h2 class="list-heading">We specialise in:</h2>
    <ul class="bullet-list">
      <li>Cut to size panels (all shapes and sizes)</li>
      <li>Plastics fabrication &amp; Welding</li>
      <li>Custom Designs</li>
      <li>Plastic Repairs</li>
      <li>PVC Pipe Slotting &amp; PVC Pipe Threading</li>
      <li>Supplier of all types of engineering plastics and profiles</li>
    </ul>
  </div>

  <div class="back__divider"></div>

  <div class="materials">
    <h2 class="list-heading">Including:</h2>
    <ul class="bullet-list">
      <li>Acrylic / Clarvene</li>
      <li>Polycarbonate / Dorvil</li>
      <li>Prismatic Light Diffuser</li>
      <li>Vantrib<span class="bullet-inline"></span>HDPE / UHMWPE</li>
      <li>PVC / PVC Foam</li>
      <li>Nylon<span class="bullet-inline"></span>HIPS</li>
    </ul>
  </div>
</section>

</body>
</html>
```